Website Redesign using existing images, copy etc.

I'm looking for a website redesign/refresh of my current WordPress website. I would like to utilize the same photography, a new photo viewer, and an overall refresh of the entire design. This will need to be WordPress with simple accessibility to make changes as we add additional properties and make updates. We auction luxury real estate and luxury yachts for non-distressed sellers. It needs to be simple, luxurious and with ease of use for both web and especially mobile. www.BrindleHarrow.com

```html
<!DOCTYPE html>
<html lang="en">
<head>
<meta charset="utf-8">
<title>Brindle Harrow — Real Estate &amp; Yachts</title>
<link rel="stylesheet" href="https://fonts.googleapis.com/css2?family=Montserrat:wght@400;500;600&display=swap">
<style>
:root{
  --ink:#1f1f1f;
  --white:#ffffff;
  --gold:#9c8a5c;
  --gold-soft:#a89a70;
  --sand:#dbd7cc;
  --taupe:#8f8468;
  --nav:rgba(122,112,100,.92);
  --footer:#000000;
  --line:#9a9a9a;
}
*{margin:0;padding:0;box-sizing:border-box}
html,body{width:1200px;height:3789px;overflow:hidden;background:var(--white)}
body{position:relative;font-family:"Montserrat",sans-serif;color:var(--ink)}
.abs{position:absolute}
.photo{position:absolute}

/* header */
.topbar{left:0;top:0;width:1200px;height:48px;background:#2a3044;color:var(--white);font-size:15px}
.topbar .phone{position:absolute;left:112px;top:14px;display:flex;align-items:center;gap:8px}
.topbar .login{position:absolute;right:112px;top:14px;display:flex;align-items:center;gap:8px}
.navbar{left:0;top:48px;width:1200px;height:68px;background:var(--nav)}
.nav-link{position:absolute;top:74px;color:var(--white);font-size:14px;letter-spacing:.5px}
.brand-mark{left:544px;top:25px;width:112px;height:112px;border:3px solid var(--white);border-radius:50%;display:flex;align-items:center;justify-content:center;color:var(--white);font-size:11px;font-weight:500;letter-spacing:1px;text-align:center;line-height:1.3}

/* hero */
.hero{left:0;top:0;width:1200px;height:685px;background:linear-gradient(180deg,#2c3350 0%,#3b3f58 45%,#4a4550 75%,#3a3a44 100%)}
.hero-title{left:0;top:312px;width:1200px;text-align:center;color:var(--white);font-size:53px;font-weight:500;letter-spacing:1px}
.hero-sub{left:0;top:398px;width:1200px;text-align:center;color:var(--white);font-size:17px;font-weight:500}
.btn-outline{position:absolute;display:flex;align-items:center;justify-content:center;border:2px solid var(--white);color:var(--white);font-size:15px;font-weight:500;outline:1px solid rgba(255,255,255,.5);outline-offset:2px}

/* intro */
.intro-shadow{left:110px;top:649px;width:375px;height:425px;background:linear-gradient(135deg,#2a2a28 0%,#3a3a36 45%,#f4f4f2 100%)}
.intro-photo{left:172px;top:598px;width:374px;height:423px;background:linear-gradient(180deg,#5d8fc4 0%,#d9a46a 40%,#5a6a3a 62%,#2c8aa8 85%,#7a6a58 100%)}
.intro-head{left:570px;top:768px;width:550px;text-align:center;color:var(--gold);font-size:27px;font-weight:500;line-height:36px;white-space:nowrap}
.intro-tag{left:590px;top:852px;width:510px;text-align:center;color:var(--gold-soft);font-size:17px}
.intro-text{left:600px;top:889px;width:490px;text-align:center;font-size:16px;line-height:29px}

/* featured */
.featured{left:0;top:1172px;width:1200px;height:629px;background:var(--sand)}
.section-head{left:0;width:1200px;text-align:center;font-size:29px;font-weight:500;letter-spacing:.5px}
.press-card{position:absolute;width:235px;height:107px;background:var(--white);box-shadow:0 1px 4px rgba(0,0,0,.12);display:flex;align-items:center;justify-content:center}
.press-badge{width:120px;height:44px;background:#c9c9c9;border-radius:3px}
.featured-text{left:628px;top:1346px;width:450px;font-size:18px;line-height:31.6px}
.btn-dark{position:absolute;display:flex;align-items:center;justify-content:center;border:2px solid #3a3a3a;font-size:18px;font-weight:500;outline:1px solid rgba(0,0,0,.3);outline-offset:2px}

/* sold */
.sold-text{left:628px;top:1953px;width:465px;height:541px;overflow:hidden;font-size:16px;line-height:31.8px}

/* about */
.about-mid{left:385px;top:2615px;width:430px;height:444px;background:var(--taupe)}
.about-head{left:385px;top:2676px;width:430px;text-align:center;font-size:30px;font-weight:500}
.about-text{left:423px;top:2744px;width:358px;height:191px;overflow:hidden;font-size:15.5px;line-height:31.8px;text-align:justify}

/* browse band */
.browse{left:0;top:3059px;width:1200px;height:169px;background:linear-gradient(180deg,#141a2c 0%,#2a2c3e 50%,#3a2e30 80%,#141018 100%)}
.browse-kicker{left:0;top:3106px;width:1200px;text-align:center;color:var(--white);font-size:17px;font-weight:500;letter-spacing:.5px}
.browse-title{left:0;top:3148px;width:1200px;text-align:center;color:var(--white);font-size:27px;font-weight:500}

/* footer */
.footer{left:0;top:3228px;width:1200px;height:561px;background:var(--footer);color:var(--white)}
.footer-mark{left:121px;top:3382px;width:100px;height:100px;border:3px solid var(--gold);border-radius:50%;display:flex;align-items:center;justify-content:center;color:var(--gold);font-size:11px;font-weight:500;letter-spacing:1px;text-align:center;line-height:1.3}
.social{position:absolute;top:3512px;width:34px;height:34px;border:2px solid var(--white);border-radius:50%}
.foot-head{position:absolute;top:3376px;color:var(--white);font-size:16px;font-weight:500;letter-spacing:.5px}
.quick-links{left:344px;top:3440px;list-style:none;font-size:17px;line-height:34.3px;font-weight:500;color:var(--white)}
.services-text{left:529px;top:3458px;width:190px;font-size:15.5px;line-height:35px;text-align:justify;font-weight:500;color:var(--white)}
.field{position:absolute;left:790px;width:298px;border-bottom:1px solid var(--line);color:var(--white);font-size:15px;font-weight:500;padding:0 0 6px 16px}
.btn-submit{position:absolute;left:790px;top:3588px;width:173px;height:45px;border:2px solid var(--white);display:flex;align-items:center;justify-content:center;color:var(--white);font-size:18px;font-weight:600;outline:1px solid rgba(255,255,255,.4);outline-offset:2px}
.copyright{left:0;top:3729px;width:1200px;text-align:center;color:var(--white);font-size:17px;font-weight:500}
</style>
</head>
<body>

<header>
  <div class="abs hero photo" role="img" aria-label="Modern glass house at dusk"></div>
  <div class="abs topbar">
    <span class="phone">
      <svg width="15" height="15" viewBox="0 0 24 24"><path fill="#fff" d="M6.6 10.8a15.1 15.1 0 0 0 6.6 6.6l2.2-2.2a1 1 0 0 1 1-.25 11.4 11.4 0 0 0 3.6.57 1 1 0 0 1 1 1V20a1 1 0 0 1-1 1A17 17 0 0 1 3 4a1 1 0 0 1 1-1h3.5a1 1 0 0 1 1 1c0 1.25.2 2.45.57 3.57a1 1 0 0 1-.25 1z"/></svg>
      555-014-2290
    </span>
    <span class="login">
      <svg width="17" height="17" viewBox="0 0 24 24" fill="none" stroke="#fff" stroke-width="1.8"><circle cx="12" cy="8" r="4.5"/><path d="M3.5 22c0-4.7 3.8-8 8.5-8s8.5 3.3 8.5 8"/></svg>
      Log in
    </span>
  </div>
  <nav class="abs navbar"></nav>
  <a class="nav-link" style="left:406px">BUY</a>
  <a class="nav-link" style="left:476px">SELL</a>
  <a class="nav-link" style="left:687px">ABOUT</a>
  <a class="nav-link" style="left:779px">CONTACT</a>
  <div class="abs brand-mark">BRINDLE<br>HARROW</div>

  <h1 class="abs hero-title">BRINDLE HARROW</h1>
  <p class="abs hero-sub">Real Estate &amp; Yachts</p>
  <a class="btn-outline" style="left:290px;top:460px;width:279px;height:40px">BROWSE UPCOMING AUCTIONS</a>
  <a class="btn-outline" style="left:632px;top:460px;width:280px;height:40px">BROWSE PAST SUCCESSES</a>
</header>

<section class="intro">
  <div class="abs intro-shadow"></div>
  <div class="abs intro-photo" role="img" aria-label="Single-storey villa with palm trees and a lit pool at sunset"></div>
  <h2 class="abs intro-head">OVER ONE BILLION DOLLARS OF<br>AUCTIONS MARKETED</h2>
  <p class="abs intro-tag">Real Estate &amp; Yachts</p>
  <p class="abs intro-text">The experience of hearing the auctioneer's final proclamation of “SOLD!” is unparalleled. Whether it's the initial meeting with the seller at their estate or yacht, or the triumphant raising of the paddle by the winning buyer, we relish every moment of the process and the ensuing festivities. We're confident that you will, too.</p>
</section>

<section class="featured-section">
  <div class="abs featured"></div>
  <h2 class="abs section-head" style="top:1258px">AS FEATURED IN</h2>
  <div class="press-card" style="left:112px;top:1356px" role="img" aria-label="Press outlet badge"><div class="press-badge"></div></div>
  <div class="press-card" style="left:365px;top:1356px" role="img" aria-label="Press outlet badge"><div class="press-badge"></div></div>
  <div class="press-card" style="left:112px;top:1479px" role="img" aria-label="Press outlet badge"><div class="press-badge"></div></div>
  <div class="press-card" style="left:365px;top:1479px" role="img" aria-label="Press outlet badge"><div class="press-badge"></div></div>
  <div class="press-card" style="left:236px;top:1603px" role="img" aria-label="Press outlet badge"><div class="press-badge" style="width:60px;height:56px"></div></div>
  <p class="abs featured-text">By offering top-tier properties and vessels globally, along with strategic auction dates, exceptional marketing tactics, and a diligent public relations team, even the most prominent media outlets have taken notice. Check out some of our latest press features.</p>
  <a class="btn-dark" style="left:628px;top:1560px;width:171px;height:40px">VIEW PRESS</a>
</section>

<section class="sold">
  <h2 class="abs section-head" style="top:1874px">SOLD BY BRINDLE HARROW</h2>
  <div class="photo" style="left:112px;top:1960px;width:237px;height:190px;background:linear-gradient(180deg,#7fa8d8 0%,#dfe6ee 55%,#5a7a9a 100%)" role="img" aria-label="White motor yacht on open water"></div>
  <div class="photo" style="left:360px;top:1960px;width:237px;height:190px;background:linear-gradient(180deg,#cfdff0 0%,#e8e8e6 50%,#6f8a58 100%)" role="img" aria-label="Modern apartment building"></div>
  <div class="photo" style="left:112px;top:2159px;width:488px;height:350px;background:linear-gradient(180deg,#4a5668 0%,#3d4654 50%,#1e2630 100%)" role="img" aria-label="Motor yacht cruising at dusk"></div>
  <a class="btn-outline" style="left:269px;top:2312px;width:172px;height:42px;font-size:18px">VIEW ALL</a>
  <p class="abs sold-text">Brindle Harrow is a top-tier destination for luxury property auctions, having overseen the auction marketing of numerous high-end estates and yachts. Our team of luxury home auction experts is committed to helping property owners obtain the best value for their assets while ensuring a timely sale. Whether you have an expansive compound or a metropolitan penthouse, Brindle Harrow has the necessary skills and expertise to facilitate various luxury real estate auctions. What's even better? Our team takes care of every aspect of the process in cooperation with tour realtor/broker, including property tours, photography and cinematography, marketing advertising, public relations and more. Apart from high-end real estate auctions, we can also organize and execute luxury yacht auctions to help boat owners find qualified buyers for their vessels. Interested in finding out</p>
</section>

<section class="about">
  <div class="photo" style="left:0;top:2615px;width:385px;height:444px;background:linear-gradient(180deg,#c8d8e6 0%,#4a5470 40%,#e8e4de 65%,#5f8a3e 100%)" role="img" aria-label="Navy craftsman house with front lawn"></div>
  <div class="abs about-mid"></div>
  <div class="photo" style="left:815px;top:2615px;width:385px;height:444px;background:linear-gradient(135deg,#e8c9a0 0%,#9ab8d8 40%,#c28a6a 70%,#f0ece6 100%)" role="img" aria-label="Friends celebrating on a sailing yacht"></div>
  <h2 class="abs about-head">ABOUT US</h2>
  <p class="abs about-text">Lorem ipsum dolor sit amet, consectetur adipiscing elit, sed do eiusmod tempor incididunt ut labore et dolore magna aliqua. Quis ipsum suspendisse ultrices gravida. Risus commodo viverra maecenas accumsan lacus vel facilisis. Lorem</p>
  <a class="btn-dark" style="left:513px;top:2965px;width:174px;height:41px">VIEW ALL</a>
</section>

<section class="browse-band">
  <div class="abs browse photo" role="img" aria-label="Calm sea at twilight"></div>
  <p class="abs browse-kicker">BROWSE</p>
  <h2 class="abs browse-title">Upcoming Auctions</h2>
</section>

<footer>
  <div class="abs footer"></div>
  <div class="abs footer-mark">BRINDLE<br>HARROW</div>
  <span class="social" style="left:121px" aria-label="Social profile"></span>
  <span class="social" style="left:183px" aria-label="Social profile"></span>
  <span class="social" style="left:245px" aria-label="Social profile"></span>

  <h3 class="foot-head" style="left:344px">QUICK LINKS</h3>
  <ul class="abs quick-links">
    <li>Home</li><li>Buy</li><li>Sell</li><li>About</li><li>Blog</li><li>Contact</li>
  </ul>

  <h3 class="foot-head" style="left:529px;font-size:15px;font-weight:600">SERVICES</h3>
  <p class="abs services-text">Lorem ipsum dolor sit amet, consectetur adipiscing elit, sed do eiusmod tempor incididunt ut labore et</p>

  <h3 class="foot-head" style="left:790px">SIGN UP FOR BRINDLE ALERTS</h3>
  <div class="field" style="top:3462px">Name</div>
  <div class="field" style="top:3515px">Email</div>
  <a class="btn-submit">SUBMIT</a>

  <p class="abs copyright">@2023 copyright Brindle Harrow &nbsp;All Right Reserved</p>
</footer>

</body>
</html>
```